Corvane Capital Business Cards

These are professional business cards that are for my family office.
Put fake emails and phone numbers as of now until I finalize those components. This family office controls my families investments, assets, and future. The cards should be professional.
..
.
.
.
I just uploaded another variation of a logo I would like to see as a business card to I am inbeteen which logo to use

Target Market(s)

business

Industry/Entity Type

business

Contact Information for Business Card

Professional, wealth related, finance related.

Requirements
Must have
• Logo

```html
<!DOCTYPE html>
<html lang="en">
<head>
<meta charset="UTF-8">
<title>Corvane Capital Business Cards</title>
<link href="https://fonts.googleapis.com/css2?family=Cinzel:wght@500&family=Montserrat:wght@400;600&display=swap" rel="stylesheet">
<style>
  :root {
    --backdrop: #2b2c2f;
    --card: #1b1f2b;
    --ink: #ffffff;
    --muted: #c9cbd1;
    --name-grey: #9a9da6;
    --rule: #8d909a;
  }
  * { box-sizing: border-box; margin: 0; padding: 0; }
  html, body {
    width: 1200px; height: 875px; overflow: hidden;
    background: var(--backdrop);
  }
  .canvas {
    width: 1200px; height: 875px;
    display: flex; flex-direction: column;
    align-items: center; justify-content: center; gap: 56px;
  }
  .card {
    width: 620px; height: 354px;
    background: var(--card);
    border-radius: 22px;
    box-shadow: 0 14px 30px rgba(0,0,0,.45);
    position: relative;
  }
  .card--front {
    display: flex; flex-direction: column;
    align-items: center; justify-content: center; gap: 26px;
  }
  .brand-ring {
    border: 3px solid var(--ink);
    border-radius: 50%;
  }
  .card--front .brand-ring { width: 150px; height: 150px; }
  .brand-name {
    font-family: "Cinzel", serif;
    font-weight: 500;
    color: var(--ink);
    letter-spacing: 2px;
  }
  .card--front .brand-name { font-size: 40px; }

  .card--back { display: flex; align-items: center; }
  .back-brand {
    width: 330px;
    display: flex; flex-direction: column; align-items: center; gap: 18px;
  }
  .back-brand .brand-ring { width: 104px; height: 104px; }
  .back-brand .brand-name { font-size: 25px; }
  .divider {
    width: 1.5px; height: 210px; background: var(--rule);
  }
  .contact {
    padding-left: 22px;
    font-family: "Montserrat", sans-serif;
    color: var(--muted);
  }
  .contact__name {
    font-weight: 600; font-size: 22px; color: var(--name-grey);
  }
  .contact__role { font-size: 13px; margin-top: 1px; }
  .contact__address { font-size: 13px; line-height: 1.3; margin-top: 22px; }
  .contact__list { list-style: none; margin-top: 16px; font-size: 13.5px; }
  .contact__list li {
    display: flex; align-items: center; gap: 9px; margin-top: 6px;
  }
  .contact__list svg { width: 13px; height: 13px; fill: var(--muted); flex: none; }
</style>
</head>
<body>
<main class="canvas">
  <section class="card card--front">
    <div class="brand-ring"></div>
    <p class="brand-name">Corvane Capital</p>
  </section>

  <section class="card card--back">
    <div class="back-brand">
      <div class="brand-ring"></div>
      <p class="brand-name">Corvane Capital</p>
    </div>
    <div class="divider"></div>
    <div class="contact">
      <p class="contact__name">Marcus Ellery</p>
      <p class="contact__role">Owner</p>
      <p class="contact__address">48 Harbor Crest Lane<br>Fairhaven, NJ 07704 USA</p>
      <ul class="contact__list">
        <li>
          <svg viewBox="0 0 24 24" aria-hidden="true"><path d="M6.6 10.8a15.1 15.1 0 0 0 6.6 6.6l2.2-2.2a1 1 0 0 1 1-.25 11.4 11.4 0 0 0 3.6.57 1 1 0 0 1 1 1V20a1 1 0 0 1-1 1A17 17 0 0 1 3 4a1 1 0 0 1 1-1h3.5a1 1 0 0 1 1 1c0 1.25.2 2.45.57 3.57a1 1 0 0 1-.25 1z"/></svg>
          (555)014-2736
        </li>
        <li>
          <svg viewBox="0 0 24 24" aria-hidden="true"><path d="M2 5h20v14H2zm2 2v.5l8 5 8-5V7l-8 5z"/></svg>
          info@corvanecapital.example
        </li>
        <li>
          <svg viewBox="0 0 24 24" aria-hidden="true"><path d="M12 2a10 10 0 1 0 0 20 10 10 0 0 0 0-20zm6.9 6h-3a15 15 0 0 0-1.3-3.9A8 8 0 0 1 18.9 8zM12 4c.9 1.2 1.6 2.5 2 4h-4c.4-1.5 1.1-2.8 2-4zM4.3 14a8 8 0 0 1 0-4h3.4a16 16 0 0 0 0 4zm.8 2h3a15 15 0 0 0 1.3 3.9A8 8 0 0 1 5.1 16zm3-8h-3a8 8 0 0 1 4.3-3.9A15 15 0 0 0 8.1 8zM12 20c-.9-1.2-1.6-2.5-2-4h4c-.4 1.5-1.1 2.8-2 4zm2.3-6H9.7a14 14 0 0 1 0-4h4.6a14 14 0 0 1 0 4zm.3 5.9a15 15 0 0 0 1.3-3.9h3a8 8 0 0 1-4.3 3.9zm1.7-5.9a16 16 0 0 0 0-4h3.4a8 8 0 0 1 0 4z"/></svg>
          www.corvanecapital.example
        </li>
      </ul>
    </div>
  </section>
</main>
</body>
</html>
```